I need a website designed. I am a mortgage loan officer and would like to have a website for me and my team where i can post resources, videos and blog information for my clients. A website like themorvaskteam.com .

The theme is - The Pelkins Team - Home Loan Group powered by Brightwell Home Loans -

Target Market(s)

B2B (Real Estate Agents)and B2C (Home buyers and refinancing)

Industry/Entity Type

Mortgage Lender

Coding

Coded - Design and coding required

Number of Pages Required

5+ page

Font styles to use
Serif
Sans Serif

Colors

Designer to choose colors to be used in the design.

Requirements
Must have
• Disclaimers: Licensed by the Bureau of Lending Affairs under the Pacific Credit Providers Act. Loans made or arranged pursuant to a Pacific Credit Providers Act License. Equal Housing Lender Brightwell Cannot Accept mortgage applications for properties located in New York via this site
• Mobile Friendly
Nice to have
• Main Links: Home, About Us(see team flyer), Mortgage 101, Contact Us (formzig form)

```html
<!DOCTYPE html>
<html lang="en">
<head>
<meta charset="utf-8">
<title>The Pelkins Team – Home Loan Group</title>
<link rel="stylesheet" href="https://fonts.googleapis.com/css2?family=Oswald:wght@400;500;600&family=Roboto:wght@300;400;500;700&display=swap">
<style>
:root{
  --blue:#1a6fc4;
  --blue-dark:#0f4f96;
  --navy:#1c2a44;
  --ink:#2b2b2b;
  --muted:#6b6f76;
  --grey-bg:#f0f1f3;
  --line:#dfe2e6;
  --footer:#222428;
  --footer-deep:#141518;
  --white:#ffffff;
}
*{box-sizing:border-box;margin:0;padding:0}
html,body{width:1200px;height:3144px;overflow:hidden}
body{font-family:"Roboto",Arial,sans-serif;color:var(--ink);background:var(--white);position:relative}
h1,h2,h3,.nav a,.btn{font-family:"Oswald","Arial Narrow",sans-serif}
section,header,footer{position:absolute;left:0;width:1200px;overflow:hidden}

/* header */
.site-header{top:0;height:100px;background:var(--white);box-shadow:0 2px 6px rgba(0,0,0,.08);z-index:3;overflow:visible}
.brand{position:absolute;left:160px;top:30px;display:flex;align-items:center;gap:12px}
.brand-square{width:34px;height:34px;background:var(--blue)}
.brand-name{font-family:"Oswald",sans-serif;font-weight:500;font-size:22px;letter-spacing:1px;color:var(--navy);text-transform:uppercase}
.nav{position:absolute;right:80px;top:0;display:flex;height:100px}
.nav a{display:flex;align-items:center;justify-content:center;width:110px;height:100px;font-size:15px;letter-spacing:1px;color:var(--navy);text-decoration:none;text-transform:uppercase}
.nav a.active{background:var(--blue);color:var(--white)}

/* hero */
.hero{top:100px;height:500px;background:linear-gradient(180deg,#6f8fa8 0%,#8ba1ad 45%,#5d6f5a 100%);text-align:center;color:var(--white)}
.hero::after{content:"";position:absolute;inset:0;background:rgba(20,35,60,.35)}
.hero-inner{position:relative;z-index:1;padding-top:150px}
.hero h1{font-size:52px;font-weight:500;letter-spacing:1px;text-transform:uppercase}
.hero p{font-size:24px;margin-top:14px;font-weight:300}
.btn{display:inline-block;background:var(--blue);color:var(--white);font-size:17px;letter-spacing:1px;text-transform:uppercase;padding:14px 36px;border-radius:30px;text-decoration:none}
.hero .btn{margin-top:34px}
.btn-outline{display:inline-block;border:2px solid var(--navy);color:var(--navy);font-family:"Oswald",sans-serif;font-size:14px;letter-spacing:1px;padding:7px 26px;border-radius:22px;text-decoration:none;text-transform:uppercase}

/* section headings */
.section-title{font-size:32px;font-weight:500;text-transform:uppercase;letter-spacing:1px;color:var(--navy);text-align:center}
.section-title span{color:var(--blue)}
.rule{width:60px;height:3px;background:var(--blue);margin:14px auto 0}

/* welcome */
.welcome{top:600px;height:450px;padding-top:46px}
.welcome .lead{width:900px;margin:22px auto 0;text-align:center;font-size:14px;line-height:1.7;color:var(--muted)}
.videos{position:absolute;top:200px;left:160px;display:flex;gap:32px}
.video{width:272px;height:200px;position:relative;background:linear-gradient(135deg,#c9d4de,#8ea2b4)}
.video svg{position:absolute;left:106px;top:70px}

/* resources */
.resources{top:1050px;height:430px;background:var(--grey-bg)}
.resources .copy{position:absolute;left:160px;top:56px;width:330px}
.resources h2{font-size:28px;font-weight:500;color:var(--blue);text-transform:uppercase}
.copy p{font-size:15px;line-height:1.7;color:var(--muted);margin-top:18px}
.copy .btn{margin-top:26px;font-size:14px;padding:10px 26px}
.resources-photo{position:absolute;left:520px;top:0;width:680px;height:430px;background:linear-gradient(120deg,#cfd9e2,#8ba0b5 60%,#5d6d80);clip-path:polygon(16% 0,100% 0,100% 100%,0 100%)}
.resources-accent{position:absolute;right:0;top:0;width:0;height:0;border-top:130px solid var(--blue);border-left:180px solid transparent}

/* team */
.team{top:1480px;height:480px;padding-top:44px}
.members{position:absolute;top:130px;left:160px;display:flex}
.member{width:220px;text-align:center;padding:0 14px}
.avatar{width:150px;height:150px;border-radius:50%;margin:0 auto;background:linear-gradient(160deg,#d8dde3,#9aa5b2);border:4px solid var(--white);box-shadow:0 0 0 2px var(--line)}
.member h3{font-size:17px;font-weight:500;color:var(--navy);text-transform:uppercase;margin-top:18px}
.member .role{font-size:13px;color:var(--blue);margin-top:4px}
.member p{font-size:13px;line-height:1.6;color:var(--muted);margin-top:10px}

/* home loan */
.home-loan{top:1960px;height:480px;background:var(--grey-bg)}
.home-loan-band{position:absolute;left:0;top:0;width:640px;height:480px;background:var(--blue);clip-path:polygon(0 0,86% 0,100% 50%,86% 100%,0 100%)}
.home-loan-photo{position:absolute;left:0;top:28px;width:610px;height:424px;background:linear-gradient(160deg,#3f5a7a,#6d7d5e 70%,#4b6a3a);clip-path:polygon(0 0,84% 0,100% 50%,84% 100%,0 100%)}
.home-loan .copy{position:absolute;left:740px;top:80px;width:320px}
.home-loan h2{font-size:28px;font-weight:500;color:var(--navy);text-transform:uppercase}

/* blog */
.blog{top:2440px;height:500px;padding-top:50px}
.posts{position:absolute;top:150px;left:160px;display:flex;gap:32px}
.post{width:272px}
.post-photo{height:140px;background:linear-gradient(135deg,#c5ced8,#8d9cad)}
.post h3{font-size:18px;font-weight:500;color:var(--navy);margin-top:20px}
.post p{font-size:13px;line-height:1.6;color:var(--muted);margin:8px 0 16px;height:42px}

/* footer */
.site-footer{top:2940px;height:204px;background:var(--footer);color:#c9ccd1}
.footer-brand{position:absolute;left:160px;top:40px;display:flex;align-items:center;gap:12px}
.footer-brand .brand-square{width:40px;height:40px}
.footer-brand .brand-name{color:var(--white);font-size:20px}
.social{position:absolute;right:160px;top:36px;display:flex;gap:12px}
.social span{width:30px;height:30px;border-radius:50%;background:var(--blue)}
.footer-links{position:absolute;right:160px;top:84px;font-size:13px;display:flex;gap:18px}
.footer-links a{color:#c9ccd1;text-decoration:none}
.disclaimer{position:absolute;left:0;bottom:0;width:1200px;height:74px;background:var(--footer-deep);padding:16px 160px;font-size:12px;line-height:1.55;color:#9a9ea5}
</style>
</head>
<body>

<header class="site-header">
  <div class="brand"><span class="brand-square"></span><span class="brand-name">The Pelkins Team</span></div>
  <nav class="nav">
    <a class="active" href="#">Home</a>
    <a href="#">About Us</a>
    <a href="#">Mortgage 101</a>
    <a href="#">Contact Us</a>
  </nav>
</header>

<section class="hero" role="img" aria-label="Couple embracing in front of a new suburban house">
  <div class="hero-inner">
    <h1>Pelkins Team, a Home Loan Company</h1>
    <p>Sed ut perspiciatis unde omnis unde omnis iste.</p>
    <a class="btn" href="#">Contact Us</a>
  </div>
</section>

<section class="welcome">
  <h2 class="section-title">Welcome to <span>The Pelkins Team Home Loan Group</span></h2>
  <p class="lead">We help families and agents move from first question to closing day with clear guidance, fair rates and steady updates. Our team explains each step and keeps every file moving so your loan stays on track.</p>
  <div class="videos">
    <div class="video" role="img" aria-label="Video still of a loan officer meeting clients">
      <svg width="60" height="60" viewBox="0 0 60 60"><circle cx="30" cy="30" r="28" fill="#1a6fc4"/><path d="M24 19 L42 30 L24 41 Z" fill="#fff"/></svg>
    </div>
    <div class="video" role="img" aria-label="Video still of a handshake over closing papers">
      <svg width="60" height="60" viewBox="0 0 60 60"><circle cx="30" cy="30" r="28" fill="#1a6fc4"/><path d="M24 19 L42 30 L24 41 Z" fill="#fff"/></svg>
    </div>
    <div class="video" role="img" aria-label="Video still of a couple reviewing loan documents">
      <svg width="60" height="60" viewBox="0 0 60 60"><circle cx="30" cy="30" r="28" fill="#1a6fc4"/><path d="M24 19 L42 30 L24 41 Z" fill="#fff"/></svg>
    </div>
  </div>
</section>

<section class="resources">
  <div class="copy">
    <h2>Resources</h2>
    <div class="rule" style="margin:12px 0 0"></div>
    <p>Browse guides, checklists and short videos that explain rates, credit, down payments and closing costs in plain words for buyers and agents alike.</p>
    <p>Each resource is kept current so you can plan your next move with confidence and share helpful tools with your clients.</p>
    <a class="btn" href="#">Download PDF</a>
  </div>
  <div class="resources-photo" role="img" aria-label="Real estate agent greeting a couple with a tablet"></div>
  <div class="resources-accent"></div>
</section>

<section class="team">
  <h2 class="section-title">Our Team</h2>
  <div class="rule"></div>
  <div class="members">
    <div class="member">
      <div class="avatar" role="img" aria-label="Portrait of Ivan Pelkins"></div>
      <h3>Ivan Pelkins</h3>
      <div class="role">Producing Branch Manager</div>
      <p>Leads the branch with years of lending experience and clear, honest advice.</p>
    </div>
    <div class="member">
      <div class="avatar" role="img" aria-label="Portrait of Tomas Ferrel"></div>
      <h3>Tomas Ferrel</h3>
      <div class="role">Loan Partner</div>
      <p>Guides buyers through options and keeps agents informed until approval.</p>
    </div>
    <div class="member">
      <div class="avatar" role="img" aria-label="Portrait of Marco Leandri"></div>
      <h3>Marco Leandri</h3>
      <div class="role">Loan Processor</div>
      <p>Reviews each file, orders appraisals and clears conditions on time.</p>
    </div>
    <div class="member">
      <div class="avatar" role="img" aria-label="Portrait of Dana Whitlow"></div>
      <h3>Dana Whitlow</h3>
      <div class="role">Closing Coordinator</div>
      <p>Schedules signings and confirms final figures so closing runs smoothly.</p>
    </div>
  </div>
</section>

<section class="home-loan">
  <div class="home-loan-band"></div>
  <div class="home-loan-photo" role="img" aria-label="Modern family home lit at dusk with a green lawn"></div>
  <div class="copy">
    <h2>Home Loan</h2>
    <div class="rule" style="margin:12px 0 0"></div>
    <p>Whether you are buying your first home, moving up or refinancing, we compare programs and find a loan that fits your budget and goals.</p>
    <p>Conventional, FHA, VA and jumbo options are available, with fast preapprovals and local support through every step of the process.</p>
  </div>
</section>

<section class="blog">
  <h2 class="section-title">Blog</h2>
  <div class="rule"></div>
  <div class="posts">
    <article class="post">
      <div class="post-photo" role="img" aria-label="Small house model with keys on a desk"></div>
      <h3>Finibus Bonorum eMalor</h3>
      <p>Quick tips on preparing your finances before you start shopping for a new home.</p>
      <a class="btn-outline" href="#">Read More</a>
    </article>
    <article class="post">
      <div class="post-photo" role="img" aria-label="Advisor reviewing paperwork with a client"></div>
      <h3>Finibus Bonorum eMalor</h3>
      <p>What lenders look for in your credit report and how to improve your score.</p>
      <a class="btn-outline" href="#">Read More</a>
    </article>
    <article class="post">
      <div class="post-photo" role="img" aria-label="Couple signing documents at a table"></div>
      <h3>Finibus Bonorum eMalor</h3>
      <p>When refinancing makes sense and how to compare offers from loan programs.</p>
      <a class="btn-outline" href="#">Read More</a>
    </article>
  </div>
</section>

<footer class="site-footer">
  <div class="footer-brand"><span class="brand-square"></span><span class="brand-name">Brightwell Home Loans</span></div>
  <div class="social"><span></span><span></span><span></span></div>
  <div class="footer-links">
    <span>All rights reserved</span>
    <a href="#">Terms &amp; Conditions</a>
    <a href="#">Privacy Policy</a>
    <a href="#">Site Map</a>
  </div>
  <div class="disclaimer">Licensed by the Bureau of Lending Affairs under the Pacific Credit Providers Act. Loans made or arranged pursuant to a Pacific Credit Providers Act License. Equal Housing Lender. Brightwell cannot accept mortgage applications for properties located in New York via this site.</div>
</footer>

</body>
</html>
```